Stationery Design Project for Nimbora, Chicago

Nimbora, a street parking application which helps car drivers find a street parking spot by offering an ideal path along which to look for parking. This path is calculated by our algorithm based on data (e.g. historical data, baseball games schedule, etc.). Along this path the driver will find a spot and will also save 70% of the search time. Customer we target is reg. between 21 and 45 yo.

We envision something young, fresh, bright and original. Slightly abstract maybe. It should represent the idea and elements of finding street parking in the city, e.g. car(s), parking spot, people, city, etc. (just ideas!).

Logo is attached.

Requirement:
- Business Cards (2 Sided Full Color CMYK)
- Letterhead (1 Sided Full Color CMYK)
- Envelope (1 Sided Full Color CMYK)
- Sticker (1 Sided Full Color CMYK), round with a 2inch diameter.

Reason: We're starting to get more and more designs and need more time to look into all of them. Very exciting!! Thanks to everybody!

Hi all, we're in the process of selecting our favs. Though choices!!! Really good submissions. Will keep you posted and sorry for the delay.

Target Market(s)

Car drivers and owners between 21 and 45

Industry/Entity Type

Parking

Requirements
Must have
• Sticker should be round and include company URL nimbora.com and the new logo which we will attach soon.
Should not have
• Should not be too serious or boring.

```html
<!DOCTYPE html>
<html lang="en">
<head>
<meta charset="utf-8">
<title>Nimbora Business Card</title>
<link href="https://fonts.googleapis.com/css2?family=Open+Sans:wght@400;600;700&display=swap" rel="stylesheet">
<style>
  :root {
    --backdrop: #d6d6d6;
    --card: #ffffff;
    --band-deep: #1c2d8c;
    --band-bright: #0b78c2;
    --rule: #0d0d0d;
    --mark-blue: #1553b8;
    --wordmark: #2e2e2e;
    --name-blue: #1d2f94;
    --title-cyan: #17a3dc;
    --body-text: #555555;
    --divider: #dddddd;
  }
  * { margin: 0; padding: 0; box-sizing: border-box; }
  html, body { width: 954px; height: 1200px; overflow: hidden; }
  body {
    position: relative;
    background: var(--backdrop);
    font-family: "Open Sans", Arial, sans-serif;
  }
  .card {
    position: absolute;
    left: 78px;
    width: 798px;
    height: 455px;
    background: var(--card);
    border-radius: 30px;
    overflow: hidden;
    box-shadow: 0 4px 14px rgba(0,0,0,0.25);
  }
  .card--front { top: 115px; }
  .card--back { top: 663px; }
  .card__band {
    position: absolute;
    left: 0; top: 0;
    width: 100%;
    height: 143px;
    background: linear-gradient(90deg, var(--band-deep) 0%, var(--band-bright) 45%, var(--band-bright) 60%, var(--band-deep) 100%);
  }
  .card__rule {
    position: absolute;
    left: 0; top: 143px;
    width: 100%;
    height: 4px;
    background: var(--rule);
  }
  .card__badge-ground {
    position: absolute;
    left: 42px; top: 85px;
    width: 226px; height: 226px;
    border-radius: 50%;
    background: var(--card);
  }
  .card__mark {
    position: absolute;
    left: 73px; top: 130px;
    width: 164px; height: 164px;
    border-radius: 50%;
    background: var(--mark-blue);
  }
  .card__wordmark {
    position: absolute;
    left: 264px; top: 162px;
    font-size: 84px;
    font-weight: 600;
    line-height: 1;
    color: var(--wordmark);
    letter-spacing: 1px;
  }
  .contact { font-size: 19px; color: var(--body-text); line-height: 26px; }
  .contact b { font-weight: 700; }
  .contact--personal {
    position: absolute;
    right: 416px; top: 330px;
    text-align: right;
  }
  .contact__name {
    font-size: 23px;
    font-weight: 700;
    color: var(--name-blue);
    margin-bottom: 22px;
  }
  .contact__title { font-size: 19px; color: var(--title-cyan); }
  .contact__divider {
    position: absolute;
    left: 400px; top: 296px;
    width: 1px; height: 145px;
    background: var(--divider);
  }
  .contact--company {
    position: absolute;
    left: 424px; top: 320px;
  }
  .contact--company .contact__gap { height: 8px; }
  .contact--footer {
    position: absolute;
    left: 0; top: 406px;
    width: 100%;
    text-align: center;
  }
</style>
</head>
<body>
  <section class="card card--front">
    <div class="card__band"></div>
    <div class="card__rule"></div>
    <div class="card__badge-ground"></div>
    <div class="card__mark"></div>
    <div class="card__wordmark">Nimbora</div>
    <div class="contact contact--personal">
      <div class="contact__name">Your Name - <span class="contact__title">Designation</span></div>
      <div><b>p</b> : 123-456-7890</div>
      <div><b>c</b> : 123-456-7890</div>
    </div>
    <div class="contact__divider"></div>
    <div class="contact contact--company">
      <div><b>e</b> : name@website.com</div>
      <div><b>w</b> : www.website.com</div>
      <div class="contact__gap"></div>
      <div>City Name, Street Name</div>
      <div>State Name, Country Code</div>
    </div>
  </section>

  <section class="card card--back">
    <div class="card__band"></div>
    <div class="card__rule"></div>
    <div class="card__badge-ground"></div>
    <div class="card__mark"></div>
    <div class="card__wordmark">Nimbora</div>
    <div class="contact contact--footer">
      <b>e</b> : name@website.com &nbsp;|&nbsp; <b>w</b> : www.website.com
    </div>
  </section>
</body>
</html>
```